Telecommunications Company needs a business card design

We are looking for a sleek, professional and modern business card design based off our new logo. Will look at both light and dark options. On some designs please provide a small space for a QR code

Target Market(s)

B2B clients in Australia

Contact Information for Business Card

Name, Position, Brisbane (head) office, Phone number, email address, QR code (link to our website qlinetelecom.com.au

Colors
0054AA
0677BA
7BADD7
CADEEF
E8F1F8
0094D4
00A9DD
6FCCEA
C7EBF8
E9F6FB
00AB8E
00BBA5
67D7C9
C6EFE9
E9F9F6

```html
<!DOCTYPE html>
<html lang="en">
<head>
<meta charset="utf-8">
<title>QLine Telecom – Business Card</title>
<link href="https://fonts.googleapis.com/css2?family=Open+Sans:wght@400;700&display=swap" rel="stylesheet">
<style>
  :root{
    --page:#1c1918;
    --card:#0d0d0d;
    --blue-deep:#0677BA;
    --blue:#0094D4;
    --blue-light:#00A9DD;
    --teal:#00BBA5;
    --grey:#9aa0a8;
    --white:#f2f4f6;
  }
  *{margin:0;padding:0;box-sizing:border-box}
  html,body{width:1200px;height:842px;overflow:hidden}
  body{
    background:var(--page);
    font-family:"Open Sans",Arial,sans-serif;
    display:flex;align-items:center;justify-content:center;gap:40px;
  }
  .card{
    position:relative;width:540px;height:309px;background:var(--card);
    overflow:hidden;box-shadow:0 10px 30px rgba(0,0,0,.5);
  }
  /* Front side */
  .band{
    position:absolute;left:0;right:0;height:11px;
    background:linear-gradient(90deg,var(--blue-light),var(--blue-deep));
  }
  .band--top{top:0}
  .band--bottom{bottom:0}
  .contact{
    position:absolute;left:0;width:100%;top:62px;
    text-align:center;color:var(--white);text-transform:uppercase;
    font-size:12.5px;line-height:1.42;letter-spacing:.2px;
  }
  .contact__name{color:var(--blue);font-weight:700;font-size:18px;line-height:1.1}
  .contact__role{font-size:12.5px}
  .rule{width:56px;height:1.5px;background:var(--blue);margin:9px auto}
  .accent{color:var(--teal)}
  /* Back side */
  .tab{position:absolute;top:118px;width:34px;height:58px;
    background:linear-gradient(180deg,var(--teal),var(--blue-deep))}
  .tab::after{content:"";position:absolute;top:0;bottom:0;width:5px;background:var(--grey)}
  .tab--left{left:0}
  .tab--left::after{right:-9px}
  .tab--right{right:0}
  .tab--right::after{left:-9px}
  .brand{
    position:absolute;inset:0;display:flex;align-items:center;justify-content:center;gap:12px;
  }
  .brand__mark{width:22px;height:22px;background:var(--blue)}
  .brand__name{color:var(--blue);font-weight:700;font-size:30px;letter-spacing:2px;text-transform:uppercase}
</style>
</head>
<body>
  <section class="card card--front" aria-label="Business card front">
    <div class="band band--top"></div>
    <div class="contact">
      <p class="contact__name">Daniel Hartley</p>
      <p class="contact__role">Managing Director</p>
      <div class="rule"></div>
      <p>044-987 321 654</p>
      <p>info@qlinetelecom.com.au</p>
      <p>www.<span class="accent">qlinetelecom</span>.com.au</p>
      <div class="rule"></div>
      <p>28 Harlow Street,</p>
      <p>Kelvin Grove, Brisbane</p>
    </div>
    <div class="band band--bottom"></div>
  </section>

  <section class="card card--back" aria-label="Business card back">
    <div class="tab tab--left"></div>
    <div class="tab tab--right"></div>
    <div class="brand">
      <span class="brand__mark"></span>
      <span class="brand__name">QLine Telecom</span>
    </div>
  </section>
</body>
</html>
```